New Bottle Label for our Velinto Grand Reserva Brandy

Graphic Design Brief
We need a new bottle label for our Brandy Gran Reserva that we want to bring to the market.
Please have a look at all our current bottles and labels and the feel of our company under www.velinto-example.ch. We would like the design to be still different to the rest - as it is not a whisky, not a fruit product, not a spirit like a gin, thus we need to create like a new family, but still fitting in with the rest of the products.
The bottle that we will be using for the brand is a different one than the one that we already have, the design of the bottle is attached with a document.
I have also attached a briefing in regards to Brandy in general for your information.
### 1. What is Brandy?
Brandy is a distilled spirit made from fermented wine or other fruit wines. It is traditionally aged in oak barrels, which gives it its characteristic color and rich flavor. The aging process in oak is essential for developing the aromas and quality of the brandy.
### 2. What is Brandy Reserva?
A Brandy labeled as "Reserva" has undergone a longer aging process, typically at least 2 to 3 years, in oak barrels. This aging gives the brandy a deeper, more complex flavor profile and a darker color. "Reserva" is often an indication of higher quality.
### 3. Who enjoys drinking Brandy?
Brandy is typically favored by those who appreciate a deep, rich tasting experience. This often includes older consumers who value the time-aged complexity of the spirit. However, Brandy is also gaining popularity among younger people, especially through cocktails and modern serving styles.
### 4. Why is Brandy trending?
Brandy is experiencing a resurgence as consumers increasingly value quality and artisanal production methods. Its versatility in cocktails and association with traditional, luxurious experiences have also contributed to its renewed popularity.
### 5. What colors would be associated with Brandy?
The typical colors associated with Brandy are warm gold, amber, and deep golden-brown tones. These colors reflect the aging process in oak barrels and the richness of the flavors. Other associated colors might include dark brown and mahogany.
### 6. What is important to customers when buying Brandy?
Customers care about the origin of the Brandy, the aging time, the quality of the ingredients, the production method, and the brand. They also pay attention to the prestige of the product and the authenticity of the production.
### 7. What is not important to customers when buying Brandy?
For many customers, the price and packaging (unless it’s especially exclusive) may be less important than the quality and taste of the Brandy. The distillery name might be less significant if it isn’t tied to a particular reputation.
### 8. What do customers know about Swiss Brandy?
Swiss Brandy is still relatively unknown in many markets, but customers who are familiar with it appreciate the precision and quality of Swiss production. Swiss Brandy is assumed to be made with care and under strict quality standards.
### 9. What is Brandy Gran Reserva?
**Brandy Gran Reserva** is an even higher quality and longer-aged version of Brandy. Generally, a Gran Reserva is aged for at least 5 to 10 years or more in oak barrels. This extended aging process gives the Brandy an especially deep, complex flavor profile and often a darker, richer color. Gran Reserva is often regarded as the top-tier product within a Brandy range and appeals to discerning consumers who value quality, refinement, and a luxurious tasting experience.
The label “Gran Reserva” thus indicates the highest quality level for Brandies, similar to other spirits (like wine or whisky), where the aging time is a critical factor.
We age our Brandy Gran Reserva in the Solara way.
### 10. What emotions are associated with Brandy?
Brandy is often associated with luxury, relaxation, and comfort. It evokes feelings of tradition, elegance, and sophistication. Drinking Brandy is frequently seen as a moment of reflection and enjoyment.
### 11. How should Brandy be marketed?
Brandy should be marketed with a focus on its artisanal production, quality, and tradition. A narrative around the product, its aging, and origin can help create an emotional connection with the customer. The marketing should also emphasize the versatility of Brandy, whether consumed neat or in cocktails.
**Label design**:
The label should reflect the exclusivity of the product, with an elegant, minimalist design. The label should include information about the aging time, the use of oak barrels, and a brief story about the Brandy’s production.
we would like to have a modern look to the whole deisgn of the brandy
Target Market(s)
Customers that like Brandy
Target Market(s)
Switzerland
Industry/Entity Type
Distillery
Look and feel

```html
<!DOCTYPE html>
<html lang="en">
<head>
<meta charset="utf-8">
<title>Velinto Grand Reserva Brandy – Label</title>
<link rel="stylesheet" href="https://fonts.googleapis.com/css2?family=Zilla+Slab:wght@700&family=EB+Garamond:wght@500&family=Teko:wght@600&family=Oswald:wght@300&family=Lato:wght@400&display=swap">
<style>
  :root {
    --navy: #021334;
    --gold: #b8954a;
    --white: #ffffff;
    --swiss-red: #e4251b;
    --page: #ffffff;
  }
  html, body {
    margin: 0;
    padding: 0;
    width: 1200px;
    height: 1200px;
    overflow: hidden;
    background: var(--page);
  }
  .canvas {
    width: 1200px;
    height: 1200px;
    display: flex;
    align-items: center;
    justify-content: center;
  }
  .label {
    width: 446px;
    height: 1004px;
    display: block;
  }
  .label-shape { fill: var(--navy); }
  .gold-frame { fill: none; stroke: var(--gold); stroke-width: 2.5; }
  .gold-rule { stroke: var(--gold); stroke-width: 2; }
  .brand-name {
    font-family: "Zilla Slab", Georgia, serif;
    font-weight: 700;
    font-size: 70px;
    fill: var(--white);
    letter-spacing: 1px;
  }
  .brand-sub {
    font-family: "Zilla Slab", Georgia, serif;
    font-weight: 700;
    font-size: 30px;
    fill: var(--white);
    letter-spacing: 1.5px;
  }
  .grade {
    font-family: "EB Garamond", Georgia, serif;
    font-weight: 500;
    font-size: 38px;
    fill: var(--white);
    letter-spacing: 5px;
  }
  .product {
    font-family: "Teko", Impact, sans-serif;
    font-weight: 600;
    font-size: 96px;
    fill: var(--white);
    letter-spacing: 5px;
  }
  .cask {
    font-family: "Oswald", "Arial Narrow", sans-serif;
    font-weight: 300;
    font-size: 46px;
    fill: var(--white);
    letter-spacing: 3px;
  }
  .web {
    font-family: "EB Garamond", Georgia, serif;
    font-weight: 500;
    font-size: 16px;
    fill: var(--white);
    letter-spacing: 2px;
  }
  .specs {
    font-family: "Lato", Arial, sans-serif;
    font-weight: 400;
    font-size: 14px;
    fill: var(--white);
  }
</style>
</head>
<body>
<main class="canvas">
  <svg class="label" viewBox="0 0 558 1256" xmlns="http://www.w3.org/2000/svg" aria-label="Velinto Grand Reserva Brandy label">
    <polygon class="label-shape" points="279,0 558,32 533,630 558,1226 279,1256 0,1226 25,630 0,32"/>
    <rect class="gold-frame" x="50" y="55" width="458" height="1147"/>

    <g class="swiss-flag">
      <rect x="268" y="126" width="22" height="22" fill="var(--swiss-red)"/>
      <rect x="277" y="130" width="4" height="14" fill="var(--white)"/>
      <rect x="272" y="135" width="14" height="4" fill="var(--white)"/>
    </g>

    <text class="brand-name" x="279" y="245" text-anchor="middle">Velinto</text>
    <text class="brand-sub" x="279" y="279" text-anchor="middle">SWISS</text>
    <text class="brand-sub" x="279" y="312" text-anchor="middle">DISTILLERY</text>

    <text class="grade" x="279" y="483" text-anchor="middle">GRAND</text>
    <text class="grade" x="279" y="528" text-anchor="middle">RESERVA</text>

    <line class="gold-rule" x1="142" y1="610" x2="415" y2="610"/>
    <text class="product" x="281" y="691" text-anchor="middle">BRANDY</text>
    <line class="gold-rule" x1="142" y1="711" x2="415" y2="711"/>

    <path id="cask-arc" d="M 130 848 Q 277 962 425 838" fill="none"/>
    <text class="cask"><textPath href="#cask-arc" startOffset="50%" text-anchor="middle">CASK STRENGHT</textPath></text>

    <text class="web" x="279" y="1061" text-anchor="middle">www.velinto-example.ch</text>

    <text class="specs" x="262" y="1189" text-anchor="end">25%</text>
    <line x1="272" y1="1172" x2="272" y2="1194" stroke="var(--white)" stroke-width="1"/>
    <text class="specs" x="282" y="1189">350ml</text>
  </svg>
</main>
</body>
</html>
```